Ridgeline Lift Works Brochure

I am looking for a multi page brochure that outlines what we do, our services, and our equipment.
We are committed to delivering equipment, operators, and technicians that provide safe, experienced, and reliable access at heights, industrial sites, power lines/facilities, construction, refineries, and other similar type industries across North America.
Our truck mounted aerial lift platforms are the preferred method of servicing at height structures and industrial plants due to their quick setup, unmatched safety, and ability to operate in adverse conditions.
Incorporate the attached images into the brochure. The overall layout should be a couple pages about us, including our commitment to safe work practices, then about the units themselves.
You can get more information from our website www.ridgelineliftpro.example
Our tagline is Safety. Quality. Service.
Colouring for the brochure should complement our red logo. Our logo could also be used as white.

```html
<!DOCTYPE html>
<html lang="en">
<head>
<meta charset="utf-8">
<title>Ridgeline Lift Works Brochure – Services</title>
<link href="https://fonts.googleapis.com/css2?family=Roboto+Slab:wght@600;700&family=Inter:wght@400;700&display=swap" rel="stylesheet">
<style>
  :root {
    --brand-red: #e8242c;
    --ink: #141414;
    --paper: #ffffff;
    --backdrop: #000000;
    --sky: #d9dde2;
    --gravel: #8f8c84;
    --grass: #5d7a34;
    --vest: #d9e81a;
  }
  * { margin: 0; padding: 0; box-sizing: border-box; }
  html, body {
    width: 1200px; height: 1200px; overflow: hidden;
    background: var(--backdrop);
  }
  .spread { position: relative; width: 1200px; height: 1200px; }
  .page {
    position: absolute; top: 180px; width: 556px; height: 788px;
    background: var(--paper); overflow: hidden;
  }
  .page--left { left: 41px; }
  .page--right { left: 602px; }

  .section-title {
    position: absolute; left: 46px; top: 42px;
    font-family: "Roboto Slab", serif; font-weight: 700;
    font-size: 41px; line-height: 1; color: var(--brand-red);
  }
  .service-heading {
    font-family: "Roboto Slab", serif; font-weight: 600;
    font-size: 20px; line-height: 23px; color: var(--ink);
  }
  .service-body {
    font-family: "Inter", sans-serif; font-size: 12.2px;
    line-height: 17px; color: var(--ink); text-align: justify;
  }
  .service-body p + p { text-indent: 59px; }

  .blade-access { position: absolute; left: 46px; top: 101px; width: 464px; }
  .blade-access .service-body { margin-top: 14px; }

  .resource-support { position: absolute; left: 46px; top: 519px; width: 464px; }
  .resource-support .service-body { margin-top: 22px; }

  .photo { position: absolute; left: 0; width: 556px; }
  .photo--trucks {
    top: 231px; height: 557px;
    background: linear-gradient(180deg, var(--sky) 0%, #c9ced3 48%, #a29f97 62%, var(--gravel) 100%);
  }
  .photo--crew {
    top: 0; height: 498px;
    background: linear-gradient(160deg, var(--grass) 0%, #8aa33a 35%, var(--vest) 70%, #c7d21c 100%);
  }

  .page-tab {
    position: absolute; top: 745px; width: 39px; height: 20px;
    background: var(--brand-red); color: var(--paper);
    font-family: "Inter", sans-serif; font-weight: 700; font-size: 10px;
    line-height: 20px; text-align: center;
  }
  .page--left .page-tab { left: 0; border-radius: 0 3px 3px 0; }
  .page--right .page-tab { right: 0; border-radius: 3px 0 0 3px; }
</style>
</head>
<body>
<main class="spread">
  <section class="page page--left">
    <h1 class="section-title">Services</h1>
    <article class="blade-access">
      <h2 class="service-heading">Blade Access</h2>
      <div class="service-body">
        <p>We provide industry leading truck mounted aerial access services using Vantora trucks. Our trucks are all less than 2 years old ensuring reliability on your project. We understand the criticality of reliability and our commitment is that your project will not be delayed as a result of equipment failure.</p>
      </div>
    </article>
    <div class="photo photo--trucks" role="img" aria-label="Two white truck mounted aerial lift units parked on a gravel yard under power lines"></div>
    <div class="page-tab">8</div>
  </section>

  <section class="page page--right">
    <div class="photo photo--crew" role="img" aria-label="Technicians in yellow hard hats and high visibility vests walking across a grassy site"></div>
    <article class="resource-support">
      <h2 class="service-heading">Supplimentary<br>Resource Support</h2>
      <div class="service-body">
        <p>As an experienced wind service provider, our goal is to provide your industry with the best trained and motivated technicians to ensure your service and maintenance needs are met with quality and on schedule. Our biggest success is when your company finds our technicians are high enough caliber to bring on board and integrate within your service organization.</p>
        <p>Our goal is also to ensure that the technicians that we provide are adequately trained and are able to integrate with your site service teams seamlessly. We only hire the highest performing technicians and ensure they are provided every opportunity for growth within their respective industries.</p>
      </div>
    </article>
    <div class="page-tab">9</div>
  </section>
</main>
</body>
</html>
```